Pallgrid App and webpage coding

We need pallgrid App and our webpage coding and uploading. I have a domain name and currently have a webpage.

Reason: This was a one-time project and the designer was working on the project. The project os completed now.

```html
<!DOCTYPE html>
<html lang="en">
<head>
<meta charset="utf-8">
<title>Dr. XYZ — Home</title>
<link href="https://fonts.googleapis.com/css2?family=Noto+Serif:wght@400;700&family=Open+Sans:wght@300;400&family=Bebas+Neue&display=swap" rel="stylesheet">
<style>
  :root{
    --page:#f4f3f1;
    --frame:#dcdcdc;
    --blue:#1b75bb;
    --band:#b9dbf0;
    --ink:#222;
    --body:#666;
    --footer:#1a77bd;
    --footer-line:#d9534f;
    --white:#fff;
  }
  *{box-sizing:border-box;margin:0;padding:0}
  html,body{width:918px;height:1200px;overflow:hidden;background:var(--white)}
  .stage{position:relative;width:1000px;height:1300px;transform:scale(.918);transform-origin:0 0;font-family:"Noto Serif",serif}
  .page{position:absolute;left:178px;top:0;width:640px;height:1300px;background:var(--page);border:1px solid var(--frame)}
  .abs{position:absolute}
  .hero{left:178px;top:13px;width:640px;height:278px;background:linear-gradient(120deg,#d9b9a4 0%,#e9cdb9 40%,#f0e2d6 70%,#e8e6e4 100%)}
  .hero-arrow{top:140px;width:24px;height:24px}
  .section-head{display:flex;align-items:center;gap:8px;height:18px;color:var(--blue);font-size:14.5px;white-space:nowrap}
  .section-head .band{flex:1;height:12px;background:var(--band)}
  .post-title{font-size:14px;color:var(--ink);white-space:nowrap}
  .post-text{font-size:11px;line-height:16px;color:var(--body)}
  .post-date{font-size:11px;color:var(--body)}
  .more{font-size:11px;color:var(--body);display:flex;align-items:center;gap:4px}
  .more::after{content:"";border-left:4px solid #555;border-top:4px solid transparent;border-bottom:4px solid transparent}
  .share-row{display:flex;gap:7px;font-size:11px;color:var(--body);align-items:center;white-space:nowrap}
  .share-row span{display:flex;align-items:center;gap:4px}
  .share-row svg{width:12px;height:12px}
  .bullets{list-style:none;font-size:11px;color:var(--body)}
  .bullets li{position:relative;padding-left:18px;height:21.7px}
  .bullets li::before{content:"";position:absolute;left:0;top:2px;width:9px;height:9px;border-radius:50%;background:var(--blue)}
  .partner{font-size:12px;line-height:14px;color:#333;display:flex;align-items:center;gap:7px}
  .partner i{display:block;flex:none;background:#333}
  .footer{left:178px;top:1194px;width:640px;height:106px;background:var(--footer);border-top:2px solid var(--footer-line);color:var(--white)}
  .footer-id{left:92px;top:24px;font-family:"Open Sans",sans-serif;font-weight:300;font-size:11px;line-height:13.5px}
  .contact-head{left:435px;top:22px;font-family:"Bebas Neue",sans-serif;font-size:16px;letter-spacing:.5px;display:flex;gap:5px;align-items:center}
  .contact-line{left:435px;font-family:"Open Sans",sans-serif;font-weight:300;font-size:11.5px;display:flex;gap:8px;align-items:center}
</style>
</head>
<body>
<div class="stage">
  <div class="page"></div>

  <div class="abs hero" role="img" aria-label="Photo of a newborn baby's face being gently touched"></div>
  <svg class="abs hero-arrow" style="left:200px" viewBox="0 0 24 24"><path d="M16 3 7 12l9 9" fill="none" stroke="#666" stroke-width="4"/></svg>
  <svg class="abs hero-arrow" style="left:756px" viewBox="0 0 24 24"><path d="M8 3l9 9-9 9" fill="none" stroke="#666" stroke-width="4"/></svg>

  <!-- What's Up America -->
  <div class="abs section-head" style="left:185px;top:336px;width:305px">What’s Up America:<span class="band"></span></div>
  <div class="abs" style="left:185px;top:366px;width:95px;height:87px;background:linear-gradient(180deg,#a9c0da,#5b6d84)" role="img" aria-label="City skyline with tall towers"></div>
  <div class="abs post-title" style="left:287px;top:363px">Excepteur sint occaecat</div>
  <p class="abs post-text" style="left:287px;top:385px;width:200px">Nemo enim ipsam voluptatem quia voluptas sit aspernatur aut odit aut fugit,&nbsp; quia consequuntur magni.</p>
  <div class="abs post-date" style="left:287px;top:440px">3 days ago.</div>
  <div class="abs more" style="left:437px;top:435px">More</div>
  <div class="abs share-row" style="left:251px;top:466px">
    <span><svg viewBox="0 0 12 12"><rect width="12" height="12" rx="1" fill="#555"/></svg>Share</span>
    <span><svg viewBox="0 0 12 12"><rect width="12" height="12" rx="1" fill="#555"/></svg>Tweet</span>
    <span><svg viewBox="0 0 14 12" style="width:14px"><rect y="1" width="14" height="10" fill="#555"/><path d="M0 1l7 6 7-6" fill="none" stroke="#f4f3f1" stroke-width="1.3"/></svg>Email</span>
    <span><svg viewBox="0 0 14 12" style="width:14px"><ellipse cx="6" cy="5" rx="5.5" ry="4" fill="none" stroke="#555" stroke-width="1.3"/><path d="M3 8l-1 3 4-2" fill="#555"/></svg>Comments</span>
  </div>

  <!-- About Me -->
  <div class="abs section-head" style="left:505px;top:336px;width:313px">About Me:<span class="band"></span></div>
  <div class="abs" style="left:505px;top:369px;width:94px;height:87px;border:4px solid #888;background:linear-gradient(150deg,#c9d4de,#eef1f3 55%,#b9473f)" role="img" aria-label="Photo of a doctor examining an infant"></div>
  <p class="abs post-text" style="left:613px;top:388px;width:200px">Temporibus autem quibusdam et aut officiis debitis aut rerum necessitatib saepe eveniet.</p>
  <div class="abs more" style="left:715px;top:438px">More</div>

  <!-- Foreign Affairs -->
  <div class="abs section-head" style="left:185px;top:557px;width:305px">Foreign Affairs/Videshi Mamle:<span class="band"></span></div>
  <div class="abs" style="left:185px;top:587px;width:95px;height:87px;background:linear-gradient(180deg,#b9c4cf,#d8d6d0 60%,#555)" role="img" aria-label="Columned government building with flags"></div>
  <div class="abs post-title" style="left:287px;top:584px">Excepteur sint occaecat</div>
  <p class="abs post-text" style="left:287px;top:607px;width:200px">Nemo enim ipsam voluptatem quia voluptas sit aspernatur aut odit aut fugit,&nbsp; quia consequuntur magni.</p>
  <div class="abs post-date" style="left:287px;top:662px">2 days ago.</div>
  <div class="abs more" style="left:437px;top:657px">More</div>
  <div class="abs share-row" style="left:251px;top:687px">
    <span><svg viewBox="0 0 12 12"><rect width="12" height="12" rx="1" fill="#555"/></svg>Share</span>
    <span><svg viewBox="0 0 12 12"><rect width="12" height="12" rx="1" fill="#555"/></svg>Tweet</span>
    <span><svg viewBox="0 0 14 12" style="width:14px"><rect y="1" width="14" height="10" fill="#555"/><path d="M0 1l7 6 7-6" fill="none" stroke="#f4f3f1" stroke-width="1.3"/></svg>Email</span>
    <span><svg viewBox="0 0 14 12" style="width:14px"><ellipse cx="6" cy="5" rx="5.5" ry="4" fill="none" stroke="#555" stroke-width="1.3"/><path d="M3 8l-1 3 4-2" fill="#555"/></svg>Comments</span>
  </div>

  <!-- Research Interests -->
  <div class="abs section-head" style="left:505px;top:557px;width:313px">My Research Interests:<span class="band"></span></div>
  <div class="abs post-title" style="left:505px;top:584px">Aliquam quaerat voluptatem</div>
  <ul class="abs bullets" style="left:505px;top:612px">
    <li>Dignissimos ducimus qui blanditiis praesentium.</li>
    <li>Consequatur aut perferendis doloribus asperiores.</li>
    <li>Voluptate velit esse quam nihil molestiae.</li>
    <li>Perferendis doloribus asperiores repellat.</li>
  </ul>
  <div class="abs more" style="left:715px;top:698px">More</div>

  <!-- Update 365 -->
  <div class="abs section-head" style="left:185px;top:778px;width:305px">Update 365:<span class="band"></span></div>
  <div class="abs" style="left:185px;top:808px;width:95px;height:87px;background:linear-gradient(170deg,#d9d2c3,#8aa7c4 55%,#d85a6a)" role="img" aria-label="Teacher with a group of young children in a classroom"></div>
  <div class="abs post-title" style="left:287px;top:805px">Omnis voluptas assumenda</div>
  <p class="abs post-text" style="left:287px;top:828px;width:205px">Duis aute irure dolor in reprehenderit in voluptate velit esse cillum dolore eu fugiat nulla pariatur suscipit.</p>
  <div class="abs post-date" style="left:287px;top:882px">3 days ago.</div>
  <div class="abs more" style="left:437px;top:878px">More</div>
  <div class="abs share-row" style="left:251px;top:908px">
    <span><svg viewBox="0 0 12 12"><rect width="12" height="12" rx="1" fill="#555"/></svg>Share</span>
    <span><svg viewBox="0 0 12 12"><rect width="12" height="12" rx="1" fill="#555"/></svg>Tweet</span>
    <span><svg viewBox="0 0 14 12" style="width:14px"><rect y="1" width="14" height="10" fill="#555"/><path d="M0 1l7 6 7-6" fill="none" stroke="#f4f3f1" stroke-width="1.3"/></svg>Email</span>
    <span><svg viewBox="0 0 14 12" style="width:14px"><ellipse cx="6" cy="5" rx="5.5" ry="4" fill="none" stroke="#555" stroke-width="1.3"/><path d="M3 8l-1 3 4-2" fill="#555"/></svg>Comments</span>
  </div>

  <!-- LensWork -->
  <div class="abs section-head" style="left:512px;top:778px;width:306px">LensWork:<span class="band"></span></div>
  <svg class="abs" style="left:778px;top:802px" width="26" height="12" viewBox="0 0 26 12"><path d="M8 1 3 6l5 5M18 1l5 5-5 5" fill="none" stroke="#777" stroke-width="2.2"/></svg>
  <div class="abs" style="left:510px;top:823px;width:143px;height:107px;background:linear-gradient(150deg,#e9ddd0,#c9a27e 50%,#2f7d4f)" role="img" aria-label="Therapist playing with colourful shapes with a young girl"></div>
  <div class="abs" style="left:668px;top:823px;width:143px;height:107px;background:linear-gradient(150deg,#e2c9a8,#c08a55 55%,#3a3836)" role="img" aria-label="Young boy using a tablet"></div>

  <!-- Partners -->
  <div class="abs partner" style="left:240px;top:1054px;width:92px"><i style="width:14px;height:14px;border-radius:50%"></i><span>Northfield State</span></div>
  <div class="abs partner" style="left:344px;top:1054px;width:142px"><i style="width:26px;height:26px;border-radius:50%"></i><span>Speech Hearing Guild</span></div>
  <div class="abs partner" style="left:284px;top:1128px;width:120px;color:var(--blue)"><i style="width:18px;height:18px;background:var(--blue)"></i><span>VoiceWell</span></div>

  <!-- Travel -->
  <div class="abs section-head" style="left:512px;top:998px;width:306px">Travel/Yatra:<span class="band"></span></div>
  <div class="abs" style="left:512px;top:1028px;width:95px;height:87px;background:linear-gradient(180deg,#6aa9da,#9cc9e4 45%,#2e6b3a 70%,#e2d2a6)" role="img" aria-label="Tropical beach with palm trees"></div>
  <div class="abs post-title" style="left:614px;top:1025px">Necessitatibus saepe</div>
  <p class="abs post-text" style="left:614px;top:1048px;width:200px">Totam rem aperiam, eaque ipsa quae ab illo inventore veritatis et quasi architecto.</p>
  <div class="abs post-date" style="left:614px;top:1102px">2 days ago.</div>
  <div class="abs more" style="left:765px;top:1097px">More</div>
  <div class="abs share-row" style="left:578px;top:1128px">
    <span><svg viewBox="0 0 12 12"><rect width="12" height="12" rx="1" fill="#555"/></svg>Share</span>
    <span><svg viewBox="0 0 12 12"><rect width="12" height="12" rx="1" fill="#555"/></svg>Tweet</span>
    <span><svg viewBox="0 0 14 12" style="width:14px"><rect y="1" width="14" height="10" fill="#555"/><path d="M0 1l7 6 7-6" fill="none" stroke="#f4f3f1" stroke-width="1.3"/></svg>Email</span>
    <span><svg viewBox="0 0 14 12" style="width:14px"><ellipse cx="6" cy="5" rx="5.5" ry="4" fill="none" stroke="#555" stroke-width="1.3"/><path d="M3 8l-1 3 4-2" fill="#555"/></svg>Comments</span>
  </div>

  <!-- Footer -->
  <footer class="abs footer">
    <div class="abs footer-id">Dr. XYZ, Ph.D.<br>Associate Professor<br>Department of ABC<br>College of yadi yadi yada</div>
    <div class="abs contact-head"><svg width="13" height="10" viewBox="0 0 14 11"><rect width="14" height="11" fill="#fff"/><path d="M0 0l7 6 7-6" fill="none" stroke="#1a77bd" stroke-width="1.4"/></svg>Contact Us</div>
    <div class="abs contact-line" style="top:50px"><svg width="12" height="9" viewBox="0 0 14 11"><rect width="14" height="11" fill="#fff"/><path d="M0 0l7 6 7-6" fill="none" stroke="#1a77bd" stroke-width="1.4"/></svg>hello@drlabnote.org</div>
    <div class="abs contact-line" style="top:70px"><svg width="11" height="11" viewBox="0 0 12 12"><path d="M2 0h3l1 3-2 1.5c1 2 2 3 3.5 3.5L9 6l3 1v3c0 1-1 2-2 2C5 12 0 7 0 2 0 1 1 0 2 0z" fill="#fff"/></svg>+ 000 555 0142</div>
  </footer>
</div>
</body>
</html>
```